Coastline Premier Retreats Business Card Design

Design a business card for Coastline Premier Retreats. Look at the website for colors and reference. Card should have logo, name, title, office number, mobile number, email, URL and a tagline like, "Luxury Hotel & Resort Email Marketing" (This might change).

https://www.coastlinepremierretreats.example

The rest I will leave up to your imagination.

Contact Information for Business Card

Logo, name, title, office number, mobile number, email, URL and a tagline like, "Luxury Hotel & Resort Email Marketing" (This might change).

```html
<!DOCTYPE html>
<html lang="en">
<head>
<meta charset="utf-8">
<title>Coastline Premier Retreats – Business Card</title>
<link href="https://fonts.googleapis.com/css2?family=Open+Sans:wght@400;600;700&display=swap" rel="stylesheet">
<style>
  :root {
    --stage: #232323;
    --card: #1f1f23;
    --orange: #f07522;
    --white: #ffffff;
    --muted: #e8e8e8;
    --rule: #bdbdbd;
  }
  * { box-sizing: border-box; margin: 0; padding: 0; }
  html, body { width: 1200px; height: 780px; overflow: hidden; background: var(--stage); }
  body { font-family: "Open Sans", Arial, sans-serif; color: var(--white); }
  .canvas {
    width: 1200px; height: 780px;
    display: flex; flex-direction: column; align-items: center; justify-content: center; gap: 26px;
  }
  .card {
    position: relative; width: 620px; height: 354px;
    background: var(--card); border-radius: 18px; overflow: hidden;
    box-shadow: 0 10px 24px rgba(0,0,0,.45);
  }
  .card__bands { position: absolute; left: 0; bottom: 0; width: 100%; height: 40px; }
  .brand-name {
    font-weight: 700; color: var(--white); text-transform: uppercase;
    letter-spacing: 1px; line-height: 1.1; text-align: center;
  }
  .card--front .brand-name {
    position: absolute; top: 128px; left: 0; width: 100%; font-size: 34px;
  }
  .card--back .brand-name {
    position: absolute; top: 142px; left: 28px; width: 230px; font-size: 20px;
  }
  .divider {
    position: absolute; left: 282px; top: 58px; width: 1px; height: 200px;
    background: linear-gradient(var(--rule), rgba(189,189,189,.2));
  }
  .contact { position: absolute; left: 312px; top: 66px; }
  .contact__name { font-size: 26px; font-weight: 700; line-height: 1.1; }
  .contact__first { color: var(--orange); }
  .contact__title { font-size: 13px; font-weight: 600; margin-top: 2px; }
  .contact__list { list-style: none; margin-top: 16px; }
  .contact__item { display: flex; align-items: center; gap: 8px; font-size: 12px; line-height: 22px; color: var(--muted); }
  .contact__icon { width: 13px; height: 13px; flex: none; }
  .tagline {
    position: absolute; right: 34px; bottom: 50px;
    font-size: 15px; color: var(--orange);
  }
</style>
</head>
<body>
<main class="canvas">

  <section class="card card--front" aria-label="Card front">
    <p class="brand-name">Coastline Premier Retreats</p>
    <svg class="card__bands" viewBox="0 0 620 40" preserveAspectRatio="none" aria-hidden="true">
      <polygon points="0,26 262,26 282,14 620,14 620,40 0,40" fill="var(--white)"/>
      <polygon points="0,26 250,26 270,40 0,40" fill="var(--orange)"/>
    </svg>
  </section>

  <section class="card card--back" aria-label="Card back">
    <p class="brand-name">Coastline Premier Retreats</p>
    <div class="divider"></div>
    <div class="contact">
      <p class="contact__name"><span class="contact__first">Marta</span> Velinska</p>
      <p class="contact__title">Managing Director</p>
      <ul class="contact__list">
        <li class="contact__item">
          <svg class="contact__icon" viewBox="0 0 16 16" aria-hidden="true"><path d="M3 1l3 3-2 2c1 2 3 4 5 5l2-2 3 3-2 2C7 14 2 9 1 3z" fill="var(--orange)"/></svg>
          (555) 201-4836
        </li>
        <li class="contact__item">
          <svg class="contact__icon" viewBox="0 0 16 16" aria-hidden="true"><rect x="4" y="1" width="8" height="14" rx="1.5" fill="none" stroke="var(--white)" stroke-width="1.5"/></svg>
          (555) 201-9090
        </li>
        <li class="contact__item">
          <svg class="contact__icon" viewBox="0 0 16 16" aria-hidden="true"><circle cx="8" cy="8" r="6.5" fill="none" stroke="var(--orange)" stroke-width="1.5"/><path d="M1.5 8h13M8 1.5c-3 3-3 10 0 13M8 1.5c3 3 3 10 0 13" fill="none" stroke="var(--orange)" stroke-width="1.2"/></svg>
          www.coastlinepremierretreats.example
        </li>
        <li class="contact__item">
          <svg class="contact__icon" viewBox="0 0 16 16" aria-hidden="true"><rect x="1" y="3" width="14" height="10" rx="1" fill="var(--orange)"/><path d="M1 4l7 5 7-5" fill="none" stroke="var(--white)" stroke-width="1.2"/></svg>
          info@coastlinepremierretreats.example
        </li>
      </ul>
    </div>
    <p class="tagline">Luxury Hotel &amp; Resort Email Marketing</p>
    <svg class="card__bands" viewBox="0 0 620 40" preserveAspectRatio="none" aria-hidden="true">
      <polygon points="0,26 262,26 282,14 620,14 620,40 0,40" fill="var(--white)"/>
      <polygon points="0,26 250,26 270,40 0,40" fill="var(--orange)"/>
    </svg>
  </section>

</main>
</body>
</html>
```